Business Intelligence Dashboard header

We are a top 10 cancer treatment clinic. Our analytics teams (Corporate Finance, Financial Analytics, and Clinical Analytics) are searching for a great graphic to show our business partners the value of our business intelligence products. We are hoping to convey that we are tech-savvy, supportive to our patients and mission of saving lives, valuable, forward-thinking, agile, supportive, and friendly.

This header will be placed at the top of each data visualization ('viz') that we create. We would like a design that is in-line with our company branding, simple, elegant, and striking. We primarily create headers that are between 800 and 1300 pixels across (800 and 1300 being the most common) and between 60 and 80 pixels high (76 being our current header height in px, but we are open to slight deviation.) The type of data visualizations this will sit atop (everything we produce, but just a few examples) will be things like patient safety, clinic utilization, appointment volumes, provider scorecards, and many more. I've included our current header, and a header I saw and liked (although I think it could have been a bit cooler.)

I'm open to ideas, feedback, and your opinion as a designer to come up with something amazing. You can find our website at https://www.harbornorthclinic.org/
Searching our business shows our main clinic (with the rounded front) https://www.findexo.com/search?q=harbor+north+oncology+partners&source=lnms&tbm=isch&sa=X&ved=0ahUKEwjjws22xuLXAhVM5mMKHb82CpQQ_AUIDCgD&biw=1995&bih=916

We are open to stock images.

Industry/Entity Type

Business

Requirements
Must have
• A place to write in a dashboard title (we will use our own BI-native object to float over the top of this banner)
Nice to have
• We would like a place/icon to differentiate between work products coming out of Clinical Analytics/Financial Analytics/Corporate Finance. We're fine with it being on 2 lines, or simply designing an icon to differentiate. We could use smaller text underneath the dashboard title (see must haves), an icon for each of the 3 teams, or a space in the header to write in the team ourselves. The team names should be of limited significance on the header. The star of the show will be the dashboard title (just leave an area for it) where the team names should be of less significance (off to the side, under the title in smaller font, etc)

```html
<!DOCTYPE html>
<html lang="en">
<head>
<meta charset="utf-8">
<title>Analytics Dashboard Headers</title>
<link rel="stylesheet" href="https://fonts.googleapis.com/css2?family=Open+Sans:wght@600;700&display=swap">
<style>
  :root {
    --page-bg: #141414;
    --band-grey: #6d6765;
    --brand-yellow: #ffc61f;
    --edge-amber: #f2a51a;
    --title-brown: #744000;
    --logo-white: #ffffff;
    --photo-amber: #d79d1a;
    --photo-deep: #c18414;
  }
  * { margin: 0; padding: 0; box-sizing: border-box; }
  html, body {
    width: 1200px; height: 573px; overflow: hidden;
    background: var(--page-bg);
    font-family: "Open Sans", Arial, sans-serif;
  }
  .canvas { position: relative; width: 1200px; height: 573px; }
  .header-banner {
    position: absolute; left: 80px; width: 1040px; height: 63px;
    background: var(--band-grey); overflow: hidden;
  }
  .header-banner--clinical { top: 110px; }
  .header-banner--corporate { top: 255px; }
  .header-banner--financial { top: 401px; }

  .banner-shape { position: absolute; inset: 0; width: 1040px; height: 63px; }
  .shape-edge { fill: var(--edge-amber); }
  .shape-fill { fill: var(--brand-yellow); }

  .brand-name {
    position: absolute; left: 21px; top: 13px;
    color: var(--logo-white); font-weight: 700;
    font-size: 10.5px; line-height: 12.5px; letter-spacing: -0.1px;
  }
  .brand-dot {
    position: absolute; left: 80px; top: 5px;
    width: 20px; height: 20px; border-radius: 50%;
    background: var(--brand-yellow);
  }

  .team-photo { position: absolute; top: 0; right: 0; height: 63px; }
  .header-banner--clinical .team-photo {
    width: 500px;
    background: linear-gradient(90deg, var(--photo-deep) 0%, var(--photo-amber) 35%, #e6ae24 60%, var(--photo-deep) 100%);
    opacity: .85;
  }
  .header-banner--corporate .team-photo {
    width: 480px;
    background: linear-gradient(90deg, rgba(255,198,31,0) 0%, var(--photo-amber) 30%, #e3aa22 60%, var(--photo-deep) 100%);
  }
  .header-banner--financial .team-photo {
    width: 530px;
    background: linear-gradient(90deg, rgba(255,198,31,0) 0%, #e9b12a 30%, var(--photo-amber) 70%, var(--photo-deep) 100%);
  }

  .team-icon { position: absolute; left: 252px; top: 17px; width: 28px; height: 28px; }
  .icon-disc { fill: var(--title-brown); }
  .icon-mark { fill: none; stroke: var(--brand-yellow); stroke-width: 2.4; stroke-linecap: round; stroke-linejoin: round; }
  .icon-solid { fill: var(--brand-yellow); }

  .dashboard-title {
    position: absolute; left: 297px; top: 12px;
    color: var(--title-brown); font-weight: 600;
    font-size: 29px; line-height: 38px; white-space: nowrap;
  }
</style>
</head>
<body>
<main class="canvas">

  <section class="header-banner header-banner--clinical">
    <svg class="banner-shape" viewBox="0 0 1040 63" aria-hidden="true">
      <path class="shape-edge" d="M116 0 C116 40 128 63 166 63 L1040 63 L1040 0 Z"/>
      <path class="shape-fill" d="M122 0 C122 38 134 61 172 63 L1040 63 L1040 0 Z"/>
    </svg>
    <div class="team-photo" role="img" aria-label="Toned photo of the main clinic building with its rounded front"></div>
    <span class="brand-dot"></span>
    <p class="brand-name">Harbor North<br>Oncology<br>Partners</p>
    <svg class="team-icon" viewBox="0 0 28 28" aria-hidden="true">
      <circle class="icon-disc" cx="14" cy="14" r="14"/>
      <path class="icon-mark" d="M4 15 H10 L12 10 L15 19 L17 13 L18.5 15 H24"/>
    </svg>
    <h2 class="dashboard-title">Clinical Analytics</h2>
  </section>

  <section class="header-banner header-banner--corporate">
    <svg class="banner-shape" viewBox="0 0 1040 63" aria-hidden="true">
      <path class="shape-edge" d="M116 0 C116 40 128 63 166 63 L1040 63 L1040 0 Z"/>
      <path class="shape-fill" d="M122 0 C122 38 134 61 172 63 L1040 63 L1040 0 Z"/>
    </svg>
    <div class="team-photo" role="img" aria-label="Toned image of gears and coins representing money and time"></div>
    <span class="brand-dot"></span>
    <p class="brand-name">Harbor North<br>Oncology<br>Partners</p>
    <svg class="team-icon" viewBox="0 0 28 28" aria-hidden="true">
      <circle class="icon-disc" cx="14" cy="14" r="14"/>
      <rect class="icon-solid" x="7" y="12" width="3.5" height="11"/>
      <rect class="icon-solid" x="12.5" y="6" width="3.5" height="17"/>
      <rect class="icon-solid" x="18" y="15" width="3.5" height="8"/>
    </svg>
    <h2 class="dashboard-title">Corporate Finance</h2>
  </section>

  <section class="header-banner header-banner--financial">
    <svg class="banner-shape" viewBox="0 0 1040 63" aria-hidden="true">
      <path class="shape-edge" d="M116 0 C116 40 128 63 166 63 L1040 63 L1040 0 Z"/>
      <path class="shape-fill" d="M122 0 C122 38 134 61 172 63 L1040 63 L1040 0 Z"/>
    </svg>
    <div class="team-photo" role="img" aria-label="Toned image of a businessman facing sketched charts and data diagrams"></div>
    <span class="brand-dot"></span>
    <p class="brand-name">Harbor North<br>Oncology<br>Partners</p>
    <svg class="team-icon" viewBox="0 0 28 28" aria-hidden="true">
      <circle class="icon-disc" cx="14" cy="14" r="14"/>
      <path class="icon-mark" d="M6 19 L11 13 L16 17 L22 9"/>
      <circle class="icon-solid" cx="11" cy="13" r="2.2"/>
      <circle class="icon-solid" cx="16" cy="17" r="2.2"/>
    </svg>
    <h2 class="dashboard-title">Financial Analytics</h2>
  </section>

</main>
</body>
</html>
```